KTWG application splash screen

We need a 1024x768 image for use as an application splash screen.
The image will be displayed full screen on an 10 inch industrial PC 1024x768 screen while our application is launching. The image should convey that the application is "Waiting for connection to Wi-Fi access point..." and include a graphic of the industrial PC connected to the access point via an Ethernet cable. A list of troubleshooting steps should be included at the bottom of the image. The troubleshooting steps should not be the main focus of the image and should be shown in a smaller font (but still readable at 1024x768 displayed on a 10 inch screen).
I will include a mock up of the general idea of what we are looking for as well as image files for the industrial PC, a screenshot of our application to show on the PC's screen and the AP.
For general look and feel and a sense of corporate branding please review our website https://marrowgatesoilworks.example/. The splash screen should reflect corporate branding.
Target Market(s)
Users of our application
Industry/Entity Type
Agriculture
Look and feel

```html
<!DOCTYPE html>
<html lang="en">
<head>
<meta charset="utf-8">
<title>KTWG – Waiting for Wi-Fi access point</title>
<link rel="stylesheet" href="https://fonts.googleapis.com/css2?family=Lexend:wght@400;600;700&display=swap">
<style>
  :root{
    --page:#000000;
    --deep:#15291e;
    --forest:#1f3d2b;
    --leaf:#3cb865;
    --mint:#6fe394;
    --glow:#9af2b6;
    --white:#ffffff;
    --ink:#111111;
  }
  *{margin:0;padding:0;box-sizing:border-box}
  html,body{width:1200px;height:1200px;overflow:hidden;background:var(--page)}
  body{position:relative;font-family:"Lexend",sans-serif}

  .splash{
    position:absolute;left:110px;top:233px;width:978px;height:734px;overflow:hidden;
    background:
      radial-gradient(ellipse 360px 260px at 930px 60px, rgba(111,227,148,.95), rgba(60,184,101,.55) 45%, transparent 75%),
      radial-gradient(ellipse 420px 200px at 120px 690px, rgba(111,227,148,.85), rgba(60,184,101,.45) 50%, transparent 80%),
      radial-gradient(ellipse 300px 220px at 980px 360px, rgba(60,184,101,.55), transparent 70%),
      radial-gradient(ellipse 500px 300px at 480px 420px, #2a4a36, transparent 75%),
      linear-gradient(160deg, #1a2f22 0%, var(--forest) 45%, var(--deep) 100%);
  }
  .splash__decor{position:absolute;inset:0;width:978px;height:734px}

  .title-card{
    position:absolute;left:283px;top:0;width:413px;height:163px;background:var(--white);
    border-radius:0 0 19px 19px;display:flex;align-items:center;justify-content:center;text-align:center;
  }
  .title-card__text{
    color:var(--leaf);font-weight:700;font-size:31.5px;line-height:34px;letter-spacing:1.2px;padding-top:22px;
  }

  .device{position:absolute;width:242px;height:242px;border-radius:50%;background:var(--white)}
  .device--pc{left:86px;top:214px}
  .device--ap{left:650px;top:214px}
  .device__art{position:absolute;display:block}
  .device--pc .device__art{left:39px;top:23px;width:165px;height:131px;border-radius:6px;
    background:linear-gradient(180deg,#2b2b2b,#151515)}
  .device--ap .device__art{left:110px;top:22px;width:24px;height:136px;border-radius:4px;
    background:linear-gradient(90deg,#e6e6e6,#fafafa 50%,#dcdcdc)}
  .device__name{position:absolute;left:0;right:0;text-align:center;color:var(--leaf);
    font-weight:700;font-size:15.5px;letter-spacing:1.1px;top:166px}
  .device--ap .device__name{font-size:14.5px;letter-spacing:.9px;top:167px}
  .device__model{position:absolute;left:0;right:0;text-align:center;color:var(--leaf);
    font-weight:400;font-size:12.5px;letter-spacing:1px;top:187px}
  .device--ap .device__model{font-size:10px;top:188px}

  .link-label{position:absolute;left:0;width:978px;top:484px;text-align:center;color:var(--white);
    font-weight:600;font-size:20.5px;letter-spacing:1.8px}

  .help-card{
    position:absolute;left:276px;top:580px;width:426px;height:154px;background:var(--white);
    border-radius:17px 17px 0 0;padding:11px 12px 0 28px;color:var(--leaf);
  }
  .help-card__title{text-align:center;font-weight:600;font-size:12.5px;letter-spacing:1px;margin-bottom:3px;padding-right:16px}
  .help-card__list,.help-card__sublist{list-style:none;font-size:10px;line-height:11.5px}
  .help-card__list>li::before,.help-card__sublist>li::before{content:"• "}
  .help-card__sublist{padding-left:12px}
  .help-card__sublist li{padding-left:7px;text-indent:-7px}

  .brand{
    position:absolute;left:856px;top:616px;width:88px;height:88px;border-radius:18px;
    background:var(--ink);border:4px solid var(--white);display:flex;align-items:center;justify-content:center;
    color:var(--white);font-weight:700;font-size:22px;letter-spacing:1px;
  }
</style>
</head>
<body>
<main class="splash">
  <svg class="splash__decor" viewBox="0 0 978 734" aria-hidden="true">
    <defs>
      <linearGradient id="shard" x1="0" y1="0" x2="1" y2="1">
        <stop offset="0" stop-color="#6fe394"/><stop offset="1" stop-color="#2f8a4d"/>
      </linearGradient>
    </defs>
    <polygon points="0,0 90,0 132,50 105,82 150,121 125,135 0,135" fill="url(#shard)" opacity=".9"/>
    <polygon points="0,135 45,135 250,135 231,110 125,110 0,110" fill="#3cb865" opacity=".55"/>
    <polygon points="740,608 978,608 978,734 820,734 858,690" fill="#3cb865" opacity=".7"/>
    <g stroke="rgba(255,255,255,.55)" stroke-width="1" fill="#e9fff0">
      <line x1="696" y1="41" x2="795" y2="41"/><circle cx="795" cy="41" r="4"/>
      <line x1="696" y1="64" x2="746" y2="64"/><circle cx="746" cy="64" r="4" fill="#9aa89f"/>
      <line x1="696" y1="76" x2="860" y2="76"/><circle cx="860" cy="76" r="4"/>
      <line x1="696" y1="99" x2="811" y2="99"/><circle cx="811" cy="99" r="4"/>
      <line x1="0" y1="204" x2="244" y2="204"/><circle cx="244" cy="204" r="4" fill="#9af2b6"/>
      <line x1="0" y1="225" x2="291" y2="225"/><circle cx="291" cy="225" r="4"/>
      <line x1="729" y1="528" x2="978" y2="528"/><circle cx="729" cy="528" r="4" fill="#9af2b6"/>
      <line x1="671" y1="554" x2="978" y2="554"/><circle cx="671" cy="554" r="4"/>
      <line x1="802" y1="568" x2="978" y2="568"/><circle cx="802" cy="568" r="4" fill="#9af2b6"/>
      <line x1="746" y1="594" x2="978" y2="594"/><circle cx="746" cy="594" r="4"/>
    </g>
    <path d="M860,30 L900,30 L978,135" fill="none" stroke="rgba(255,255,255,.7)" stroke-width="1.5"/>
    <path d="M208,471 V517 H770 V471" fill="none" stroke="#ffffff" stroke-width="3.5" stroke-dasharray="0 9.6" stroke-linecap="round"/>
  </svg>

  <header class="title-card">
    <h1 class="title-card__text">Waiting for<br>connection to Wi-Fi<br>access point...</h1>
  </header>

  <section class="device device--pc">
    <span class="device__art" role="img" aria-label="Rugged tractor cab tablet computer showing the KTWG application"></span>
    <p class="device__name">TRACTOR CAB</p>
    <p class="device__model">COMPUTER</p>
  </section>

  <section class="device device--ap">
    <span class="device__art" role="img" aria-label="White outdoor Wi-Fi access point with two antennas"></span>
    <p class="device__name">WI-FI ACCESS POINT</p>
    <p class="device__model">NORLINK AX220-OUTDOOR</p>
  </section>

  <p class="link-label">ETHERNET CABLE</p>

  <section class="help-card">
    <h2 class="help-card__title">TROUBLESHOOTING STEPS:</h2>
    <ul class="help-card__list">
      <li>This screen should only be visible for a short time on boot.</li>
      <li>If this screen stays visible for more than a minute:
        <ul class="help-card__sublist">
          <li>Verify that the Wi-Fi Access Point (AP) powers up when this system does<br>(indicated by a green light on the side of the AP).</li>
          <li>Check the Ethernet cable between this system and the AP for damage,<br>and replace it if necessary.</li>
          <li>Power-cycle this system and wait for it to reboot fully.</li>
          <li>If the issue persists, contact KTWG support for further assistance.</li>
        </ul>
      </li>
    </ul>
  </section>

  <div class="brand">KTWG</div>
</main>
</body>
</html>
```